New professional Training Site

I need a basic 4-page Wordpress website using an existing logo that I will supply.  I would like appropriate images to complement the text which I have provided. I would like a link on the landing page to a brochure of 4 pages, which I shall also provide.

I have attached the various Logo files, the text for the pages, and the pages of the brochure.
Here is the brochure in question: https://www.plivomarket.com/design/28021656

The market is professional business training, and the target audience is buyers and sellers of businesses.

I would like an editable box on the landing page to list ‘Future Events’.

Updates
I still have no access to the site I want made over, so there is nothing we can do at present.

Target Market(s)
Buyers and sellers of businesses
Industry/Entity Type
Professional Training
Coding
Coded - Design and coding required
Number of Pages Required
4 page
Font styles to use
Other font styles liked:
- Helvetica Neue

Requirements
Must have
- The 4 pages structure as set out in the attached word doc. An editable box on the landing page for "Upcoming Events'

Nice to have
- I want the designs to feature the colours and log attached.

```html
<!DOCTYPE html>
<html lang="en">
<head>
<meta charset="utf-8">
<title>Accord Academy – Home Page Concepts</title>
<link href="https://fonts.googleapis.com/css2?family=Montserrat:wght@400;500;600;700;800&display=swap" rel="stylesheet">
<style>
  :root{
    --navy:#1f3566;
    --navy-deep:#172a52;
    --red:#a4212b;
    --red-bright:#c8202f;
    --text:#555a63;
    --muted:#8a8e95;
    --white:#ffffff;
    --band:#eeeded;
  }
  *{box-sizing:border-box;margin:0;padding:0}
  html,body{width:880px;height:1200px;overflow:hidden}
  body{
    font-family:"Montserrat",Helvetica,Arial,sans-serif;
    background:linear-gradient(120deg,#e6b7bd 0%,#c9c0cf 45%,#b7bccc 100%);
    position:relative;
  }
  .page{
    position:absolute;top:95.9px;width:627px;height:1893px;
    background:var(--white);transform:scale(0.5327);transform-origin:0 0;overflow:hidden;
  }
  .page--city{left:66.6px}
  .page--office{left:451.7px}
  .abs{position:absolute}

  .top-rule{position:absolute;top:0;left:0;width:100%;height:4px;
    background:linear-gradient(90deg,var(--red) 0 50%,var(--navy) 50% 100%)}
  .brand{position:absolute;left:78px;top:18px;display:flex;align-items:center;gap:6px}
  .brand-dot{width:30px;height:30px;border-radius:50%;background:var(--navy)}
  .brand-name{font-weight:800;font-size:12px;line-height:1.05;color:var(--navy);letter-spacing:.3px;width:80px}
  .main-nav{position:absolute;top:28px;left:237px;display:flex;gap:0}
  .main-nav a{font-size:8.3px;font-weight:700;color:var(--navy);text-decoration:none;letter-spacing:.2px}
  .main-nav a:nth-child(1){margin-right:24px}
  .main-nav a:nth-child(2){margin-right:24px}
  .main-nav a:nth-child(3){margin-right:22px}

  .hero{position:absolute;top:58px;left:0;width:627px;height:375px}
  .hero-title{position:absolute;top:100px;width:627px;text-align:center;color:var(--white);
    font-weight:800;font-size:33px;letter-spacing:.5px;text-shadow:0 2px 6px rgba(0,0,0,.35)}
  .btn{position:absolute;left:266px;width:95px;height:28px;border-radius:14px;
    background:linear-gradient(90deg,var(--navy) 0%,var(--navy) 55%,var(--red) 100%);
    color:var(--white);font-size:8px;font-weight:700;display:flex;align-items:center;justify-content:center;letter-spacing:.2px}
  .btn--hero{top:205px}
  .btn--events{top:1604px}

  .emblem{position:absolute;left:85px;top:505px;width:200px;height:270px;display:flex;flex-direction:column;align-items:center;gap:18px}
  .emblem-disc{width:190px;height:190px;border-radius:50%;background:var(--navy)}
  .emblem-name{font-weight:800;font-size:16px;color:var(--red);letter-spacing:.5px}
  .intro{position:absolute;left:318px;top:515px;width:228px}
  .intro h2{font-size:18.5px;line-height:22px;font-weight:800;color:var(--navy);letter-spacing:.2px}
  .intro h2 .accent{color:var(--red)}
  .intro p{font-size:7.6px;line-height:10.3px;color:var(--text);margin-top:11px}
  .intro h2 + p{margin-top:19px}

  .package{position:absolute;top:818px;left:0;width:627px;height:362px}
  .package-lead{position:absolute;top:882px;left:0;width:650px;text-align:center;font-size:12.4px;line-height:15px;font-weight:600;color:#33363c}
  .offer{position:absolute;border-radius:50%;color:var(--white);text-align:center;display:flex;flex-direction:column;align-items:center}
  .offer--navy{background:var(--navy)}
  .offer--red{background:var(--red);border:2px solid var(--white);box-shadow:0 0 0 1.5px var(--red)}
  .offer-1{left:79px;top:940px;width:156px;height:156px}
  .offer-2{left:226px;top:931px;width:174px;height:174px;z-index:2}
  .offer-3{left:392px;top:940px;width:156px;height:156px}
  .offer svg{margin-top:30px}
  .offer-2 svg{margin-top:39px}
  .offer h3{font-size:10.8px;line-height:13px;font-weight:700;margin-top:8px}
  .offer a{font-size:7.8px;font-weight:600;color:var(--white);margin-top:13px;text-decoration:underline}

  .events-title{position:absolute;top:1247px;width:627px;text-align:center;font-size:24px;font-weight:800;color:var(--navy);letter-spacing:.3px}
  .events-title .accent{color:var(--red)}
  .photo{position:absolute}
  .photo-lead{left:78px;top:1300px;width:206px;height:280px;background:linear-gradient(160deg,#3b6f8a 0%,#8a6a4a 40%,#2b2e38 100%)}
  .photo-s1{left:299px;top:1300px;width:93px;height:83px;background:linear-gradient(150deg,#d7dde3,#54606e)}
  .photo-s2{left:299px;top:1398px;width:93px;height:83px;background:linear-gradient(150deg,#7c7e80,#b9a796 60%,#4c4a4a)}
  .photo-s3{left:299px;top:1496px;width:93px;height:83px;background:linear-gradient(150deg,#eef0f2,#4e5256)}
  .event{position:absolute;left:403px;width:150px}
  .event time{display:block;font-size:6.8px;color:var(--red);font-weight:500}
  .event h4{font-size:9.8px;line-height:11.5px;font-weight:600;color:#4a4d53;margin-top:7px}
  .event p{font-size:6.7px;line-height:9px;color:var(--muted);margin-top:9px}
  .event-1{top:1303px}
  .event-2{top:1401px}
  .event-3{top:1499px}

  .footer{position:absolute;top:1660px;left:0;width:627px;height:233px}
  .footer-brand{position:absolute;top:1708px;left:262px;display:flex;align-items:center;gap:6px}
  .footer-brand .brand-dot{width:36px;height:36px;background:var(--white)}
  .footer-brand .brand-name{color:var(--white);font-size:13.5px;width:90px}
  .footer-nav{position:absolute;top:1777px;left:0;width:627px;display:flex;justify-content:center;gap:24px;padding-left:4px}
  .footer-nav a{font-size:8.3px;font-weight:700;color:var(--white);text-decoration:none}
  .copyright{position:absolute;top:1815px;width:627px;text-align:center;font-size:7.6px;color:#d9dde8;letter-spacing:.2px}
  .social{position:absolute;top:1853px;left:285px;display:flex;gap:7px}
  .social span{width:16px;height:16px;border-radius:50%;background:var(--white)}
  .social span:first-child{background:var(--red-bright)}
</style>
</head>
<body>

<!-- Concept A -->
<article class="page page--city">
  <div class="top-rule"></div>
  <div class="brand"><span class="brand-dot"></span><span class="brand-name">ACCORD ACADEMY</span></div>
  <nav class="main-nav"><a>HOME</a><a>WORKSHOP</a><a>THE DIRECTORS' CIRCLE</a><a>HELP-LINE</a></nav>

  <svg class="hero" viewBox="0 0 627 375" role="img" aria-label="Photo of two business people shaking hands over a night city skyline">
    <defs>
      <linearGradient id="heroCity" x1="0" y1="0" x2="0.6" y2="1">
        <stop offset="0" stop-color="#2a3147"/>
        <stop offset="0.3" stop-color="#c76a82"/>
        <stop offset="0.55" stop-color="#7b5a5e"/>
        <stop offset="1" stop-color="#1c2333"/>
      </linearGradient>
    </defs>
    <path d="M0 0 H627 V322 Q313 422 0 322 Z" fill="url(#heroCity)"/>
  </svg>
  <h1 class="hero-title">ACCORD ACADEMY</h1>
  <div class="btn btn--hero">VIEW CLASSES</div>

  <div class="emblem"><span class="emblem-disc"></span><span class="emblem-name">ACCORD ACADEMY</span></div>
  <section class="intro">
    <h2>A NEW APPROACH TO<br>BUYING OR <span class="accent">SELLING</span><br><span class="accent">A BUSINESS</span></h2>
    <p>We are a small group of experienced entrepreneurs, bankers, accountants, and others who have between us many decades of buying, selling, and founding businesses of all types and sizes, few if any of which had a turnover of less than several £ millions.</p>
    <p>We provide both first-time entrepreneurs and more experienced deal-doers with an unrivalled package of help, services, and support to enable them to successfully acquire SME businesses.</p>
    <p>We believe that the skills we provide at our workshops although vital are not enough on their own. Entrepreneurs need continuing support and advice both before and after they have made their investment.</p>
  </section>

  <svg class="package" viewBox="0 0 627 362" role="img" aria-label="Faded photo of a meeting room behind the package section">
    <path d="M0 62 Q313 -60 627 62 V300 Q313 420 0 300 Z" fill="var(--band)"/>
  </svg>
  <p class="package-lead">Our package comprises both initial<br>skills training and continuing support</p>

  <div class="offer offer--navy offer-1">
    <svg width="36" height="38" viewBox="0 0 36 38" fill="none" stroke="#fff" stroke-width="2"><rect x="4" y="2" width="18" height="14"/><circle cx="27" cy="7" r="3" fill="#fff"/><path d="M27 11v12M24 14h6"/><path d="M2 36h32M6 30h6M16 30h6"/><circle cx="9" cy="25" r="2.5" fill="#fff"/><circle cx="19" cy="25" r="2.5" fill="#fff"/></svg>
    <h3>Accord Academy<br>Workshop</h3><a>Click Here</a>
  </div>
  <div class="offer offer--red offer-2">
    <svg width="38" height="38" viewBox="0 0 38 38" fill="none" stroke="#fff" stroke-width="2"><circle cx="19" cy="11" r="7"/><path d="M5 36c0-9 6-14 14-14s14 5 14 14z"/><path d="M2 36h34"/></svg>
    <h3>The Directors'<br>Circle</h3><a>Click Here</a>
  </div>
  <div class="offer offer--navy offer-3">
    <svg width="36" height="38" viewBox="0 0 36 38" fill="none" stroke="#fff" stroke-width="2"><circle cx="18" cy="13" r="8"/><path d="M8 13a10 10 0 0 1 20 0M6 12v5M30 12v5"/><path d="M4 36c0-8 6-12 14-12s14 4 14 12z"/></svg>
    <h3>Deals<br>Help-Line</h3><a>Click Here</a>
  </div>

  <h2 class="events-title">FUTURE <span class="accent">EVENTS</span></h2>
  <div class="photo photo-lead" role="img" aria-label="Photo of an audience listening to a speaker"></div>
  <div class="photo photo-s1" role="img" aria-label="Photo of a seminar presentation"></div>
  <div class="photo photo-s2" role="img" aria-label="Photo of a speaker with a microphone"></div>
  <div class="photo photo-s3" role="img" aria-label="Photo of a business discussion"></div>
  <div class="event event-1"><time>Jan 27 2022</time><h4>Lorem ipsum dolor sit ame consectetur adipiscing.</h4><p>Lorem ipsum dolor sit amet, consectetur adipis cing elit, sed do eiusmod tempor incididunt ut labore et dolore</p></div>
  <div class="event event-2"><time>Jan 27 2022</time><h4>Lorem ipsum dolor sit ame consectetur adipiscing.</h4><p>Lorem ipsum dolor sit amet, consectetur adipis cing elit, sed do eiusmod tempor incididunt ut labore et dolore</p></div>
  <div class="event event-3"><time>Jan 27 2022</time><h4>Lorem ipsum dolor sit ame consectetur adipiscing.</h4><p>Lorem ipsum dolor sit amet, consectetur adipis cing elit, sed do eiusmod tempor incididunt ut labore et dolore</p></div>
  <div class="btn btn--events">VIEW MORE</div>

  <svg class="footer" viewBox="0 0 627 233">
    <path d="M0 68 Q313 -45 627 68" fill="none" stroke="var(--red)" stroke-width="5"/>
    <path d="M0 82 Q313 -28 627 82 V233 H0 Z" fill="var(--navy)"/>
  </svg>
  <div class="footer-brand"><span class="brand-dot"></span><span class="brand-name">ACCORD ACADEMY</span></div>
  <nav class="footer-nav"><a>HOME</a><a>WORKSHOP</a><a>THE DIRECTORS' CIRCLE</a><a>HELP-LINE</a></nav>
  <p class="copyright">©2022 ACCORD ACADEMY.&nbsp; ALL RIGHTS RESERVED.</p>
  <div class="social" aria-label="Social links"><span></span><span></span><span></span></div>
</article>

<!-- Concept B -->
<article class="page page--office">
  <div class="top-rule"></div>
  <div class="brand"><span class="brand-dot"></span><span class="brand-name">ACCORD ACADEMY</span></div>
  <nav class="main-nav"><a>HOME</a><a>WORKSHOP</a><a>THE DIRECTORS' CIRCLE</a><a>HELP-LINE</a></nav>

  <svg class="hero" viewBox="0 0 627 375" role="img" aria-label="Photo of a team meeting in a bright office with a presenter at a whiteboard">
    <defs>
      <linearGradient id="heroOffice" x1="0" y1="0" x2="1" y2="1">
        <stop offset="0" stop-color="#c9ccd1"/>
        <stop offset="0.45" stop-color="#eef0f2"/>
        <stop offset="0.75" stop-color="#9aa6b8"/>
        <stop offset="1" stop-color="#3c55a0"/>
      </linearGradient>
    </defs>
    <path d="M0 0 H627 V322 Q313 422 0 322 Z" fill="url(#heroOffice)"/>
  </svg>
  <h1 class="hero-title">ACCORD ACADEMY</h1>
  <div class="btn btn--hero">VIEW CLASSES</div>

  <div class="emblem"><span class="emblem-disc"></span><span class="emblem-name">ACCORD ACADEMY</span></div>
  <section class="intro">
    <h2>A NEW APPROACH TO<br>BUYING OR <span class="accent">SELLING</span><br><span class="accent">A BUSINESS</span></h2>
    <p>We are a small group of experienced entrepreneurs, bankers, accountants, and others who have between us many decades of buying, selling, and founding businesses of all types and sizes, few if any of which had a turnover of less than several £ millions.</p>
    <p>We provide both first-time entrepreneurs and more experienced deal-doers with an unrivalled package of help, services, and support to enable them to successfully acquire SME businesses.</p>
    <p>We believe that the skills we provide at our workshops although vital are not enough on their own. Entrepreneurs need continuing support and advice both before and after they have made their investment.</p>
  </section>

  <svg class="package" viewBox="0 0 627 362" role="img" aria-label="Faded photo of a meeting room behind the package section">
    <path d="M0 62 Q313 -60 627 62 V300 Q313 420 0 300 Z" fill="var(--band)"/>
  </svg>
  <p class="package-lead">Our package comprises both initial<br>skills training and continuing support</p>

  <div class="offer offer--navy offer-1">
    <svg width="36" height="38" viewBox="0 0 36 38" fill="none" stroke="#fff" stroke-width="2"><rect x="4" y="2" width="18" height="14"/><circle cx="27" cy="7" r="3" fill="#fff"/><path d="M27 11v12M24 14h6"/><path d="M2 36h32M6 30h6M16 30h6"/><circle cx="9" cy="25" r="2.5" fill="#fff"/><circle cx="19" cy="25" r="2.5" fill="#fff"/></svg>
    <h3>Accord Academy<br>Workshop</h3><a>Click Here</a>
  </div>
  <div class="offer offer--red offer-2">
    <svg width="38" height="38" viewBox="0 0 38 38" fill="none" stroke="#fff" stroke-width="2"><circle cx="19" cy="11" r="7"/><path d="M5 36c0-9 6-14 14-14s14 5 14 14z"/><path d="M2 36h34"/></svg>
    <h3>The Directors'<br>Circle</h3><a>Click Here</a>
  </div>
  <div class="offer offer--navy offer-3">
    <svg width="36" height="38" viewBox="0 0 36 38" fill="none" stroke="#fff" stroke-width="2"><circle cx="18" cy="13" r="8"/><path d="M8 13a10 10 0 0 1 20 0M6 12v5M30 12v5"/><path d="M4 36c0-8 6-12 14-12s14 4 14 12z"/></svg>
    <h3>Deals<br>Help-Line</h3><a>Click Here</a>
  </div>

  <h2 class="events-title">FUTURE <span class="accent">EVENTS</span></h2>
  <div class="photo photo-lead" role="img" aria-label="Photo of an audience listening to a speaker"></div>
  <div class="photo photo-s1" role="img" aria-label="Photo of a seminar presentation"></div>
  <div class="photo photo-s2" role="img" aria-label="Photo of a speaker with a microphone"></div>
  <div class="photo photo-s3" role="img" aria-label="Photo of a business discussion"></div>
  <div class="event event-1"><time>Jan 27 2022</time><h4>Lorem ipsum dolor sit ame consectetur adipiscing.</h4><p>Lorem ipsum dolor sit amet, consectetur adipis cing elit, sed do eiusmod tempor incididunt ut labore et dolore</p></div>
  <div class="event event-2"><time>Jan 27 2022</time><h4>Lorem ipsum dolor sit ame consectetur adipiscing.</h4><p>Lorem ipsum dolor sit amet, consectetur adipis cing elit, sed do eiusmod tempor incididunt ut labore et dolore</p></div>
  <div class="event event-3"><time>Jan 27 2022</time><h4>Lorem ipsum dolor sit ame consectetur adipiscing.</h4><p>Lorem ipsum dolor sit amet, consectetur adipis cing elit, sed do eiusmod tempor incididunt ut labore et dolore</p></div>
  <div class="btn btn--events">VIEW MORE</div>

  <svg class="footer" viewBox="0 0 627 233">
    <path d="M0 68 Q313 -45 627 68" fill="none" stroke="var(--red)" stroke-width="5"/>
    <path d="M0 82 Q313 -28 627 82 V233 H0 Z" fill="var(--navy)"/>
  </svg>
  <div class="footer-brand"><span class="brand-dot"></span><span class="brand-name">ACCORD ACADEMY</span></div>
  <nav class="footer-nav"><a>HOME</a><a>WORKSHOP</a><a>THE DIRECTORS' CIRCLE</a><a>HELP-LINE</a></nav>
  <p class="copyright">©2022 ACCORD ACADEMY.&nbsp; ALL RIGHTS RESERVED.</p>
  <div class="social" aria-label="Social links"><span></span><span></span><span></span></div>
</article>

</body>
</html>
```